Agriculture farming Hemp and CBD

The logo is in works with your company now, should be ready in a few days. We have our Domain (kestrelbrookhollow.com) We would like to see incorporated seed to growth, but not necessary. we would like to nature colors and some black and green. we have our farm and will be growing and selling HEMP and CBD we are based in the state of Virginia. Would like to incorporate the words pause, play, rewind if possible but not necessary.

Target Market(s)

20 years old to elderly

Coding

Coded - Design and coding required

Number of Pages Required

3 page

Font styles to use
Serif

Requirements
Must have
• I'm not sure on the must haves, we are open to any ideas, we would definitely like to see Hemp and CBD included, may the life cycle of seed to plant. We must have a pop up asking if you are 20 years old before they can enter our site and to view or purchase our product. I want the design to be totally different than what i uploaded.
Nice to have
• Would like to see natural colors as well as black and green
Should not have
• I want

```html
<!DOCTYPE html>
<html lang="en">
<head>
<meta charset="utf-8">
<title>Kestrel Brook Hollow – Home</title>
<link href="https://fonts.googleapis.com/css2?family=Hind:wght@400;500;600&family=Arimo:wght@400&display=swap" rel="stylesheet">
<style>
:root{
  --canvas:#ededee;
  --black:#0a0a0a;
  --charcoal:#161616;
  --green:#1ed61a;
  --green-deep:#0d8f0d;
  --green-dark:#0b5f0b;
  --white:#ffffff;
  --ink:#222222;
  --muted:#555555;
}
*{box-sizing:border-box;margin:0;padding:0}
html,body{width:728px;height:1200px;overflow:hidden;background:var(--canvas)}
body{position:relative;font-family:"Arimo",Arial,sans-serif}
.panel{position:absolute;top:22px;width:340px;height:1147px;background:var(--white);overflow:hidden;box-shadow:0 0 0 .5px #d4d4d4}
.panel--gate{left:18px}
.panel--open{left:372px}
.panel>*{position:absolute}
.backdrop{left:0;top:0;width:340px;height:1147px}
.heading{font-family:"Hind",sans-serif;font-weight:600;line-height:1}
.brand{font-family:"Hind",sans-serif;font-weight:600;color:var(--white);white-space:nowrap;line-height:1}
.nav{display:flex;gap:8px;font-family:"Hind",sans-serif;font-size:4.6px;color:var(--white);white-space:nowrap;line-height:1}
.nav .is-active{color:var(--green)}
.copy{font-size:3.9px;line-height:7.5px;color:var(--muted);text-align:justify}
.btn{display:flex;align-items:center;justify-content:center;font-family:"Hind",sans-serif;font-weight:600;font-size:4.4px;color:var(--white);letter-spacing:.1px}
.btn--green{background:var(--green);border-radius:1px}
.btn--dark{background:#151515;border-radius:1px}

.header-brand{left:32px;top:14px;font-size:10px}
.header-nav{left:156px;top:17px}
.cart{left:301px;top:15px;width:8px;height:7px}

.hero-frame{left:0;top:0;width:340px;height:240px}
.hero-brand{left:0;top:118px;width:340px;text-align:center;font-size:17px}
.hero-tag{left:65px;top:141px;width:209px;text-align:center;font-family:"Hind",sans-serif;font-weight:600;font-size:15px;color:var(--green);letter-spacing:1.2px;line-height:1}

.about-title{left:32px;top:288px;font-size:14px;color:var(--ink)}
.about-sub{left:32px;top:304px;font-size:11.5px;color:var(--green)}
.about-copy{left:32px;top:322px;width:139px}
.about-btn{left:32px;top:385px;width:41px;height:15px}
.about-leaf{left:182px;top:282px;width:128px;height:122px;border-radius:4px;background:linear-gradient(160deg,#5ea83c 0%,#3b8427 45%,#24621a 100%)}

.growth-visual{left:39px;top:457px;width:122px;height:122px;border-radius:50%;background:linear-gradient(135deg,#7ad957 0%,#3ea82a 40%,#1f7a17 75%,#15590f 100%);border:3px solid #2ee524}
.growth-kicker{left:172px;top:467px;font-size:13px;color:var(--ink)}
.growth-title{left:172px;top:481px;font-size:17.5px;color:var(--ink)}
.growth-copy{left:172px;top:504px;width:131px;color:#103a10}
.growth-btn{left:172px;top:557px;width:41px;height:15px}

.services-title{left:0;top:632px;width:340px;text-align:center;font-size:14.5px;color:var(--white)}
.services-rule{left:163px;top:650px;width:14px;height:1px;background:var(--green)}
.service{top:663px;width:94px;text-align:center}
.service--1{left:29px}.service--2{left:123px}.service--3{left:216px}
.service-icon{display:block;margin:0 auto;width:46px;height:46px}
.service h3{font-family:"Hind",sans-serif;font-weight:600;font-size:7.5px;color:var(--white);margin-top:5px;line-height:1}
.service p{width:70px;margin:3px auto 0;font-size:3.8px;line-height:7.2px;color:#e4e4e4}

.news-title{left:0;top:796px;width:340px;text-align:center;font-size:12.5px;color:var(--ink)}
.news-title b{color:var(--green);font-weight:600}
.news-rule{left:163px;top:812px;width:14px;height:1px;background:var(--ink)}
.news-card{top:824px;width:89px}
.news-card--1{left:32px}.news-card--2{left:126px}.news-card--3{left:219px}
.news-photo{width:89px;height:66px}
.news-photo--seed-hands{background:linear-gradient(135deg,#e6dccd,#c7a87c 50%,#8a6a44)}
.news-photo--leaves{background:linear-gradient(135deg,#4fb02c,#2a8019 55%,#15500e)}
.news-photo--seeds{background:linear-gradient(135deg,#c4b8a6,#8f7b66 55%,#5a4838)}
.news-card h4{font-family:"Hind",sans-serif;font-weight:600;font-size:3.9px;line-height:7px;color:var(--ink);margin-top:6px;letter-spacing:.05px}
.news-card p{font-size:3.7px;line-height:8px;color:var(--muted);margin-top:3px;text-align:justify}
.news-card .btn{width:32px;height:12px;margin-top:5px;font-size:3.9px}

.news-letter-title{left:0;top:991px;width:340px;text-align:center;font-size:12.5px;color:var(--ink)}
.news-letter-rule{left:163px;top:1007px;width:14px;height:1px;background:var(--ink)}
.news-letter-copy{left:70px;top:1015px;width:200px;text-align:center;font-family:"Hind",sans-serif;font-size:4.4px;line-height:8.5px;color:#0d4d0d}
.email-field{left:71px;top:1043px;width:200px;height:15px;border:.7px solid #0f5a0f;font-family:"Hind",sans-serif;font-size:4.3px;color:#0f3f0f;padding:5px 6px}
.submit-btn{left:145px;top:1064px;width:51px;height:16px;font-size:4.8px}

.footer-brand{left:0;top:1115px;width:340px;text-align:center;font-size:10px}
.footer-nav{left:0;top:1134px;width:340px;justify-content:center;font-size:4.4px}
.copyright{left:0;top:1149px;width:340px;text-align:center;font-family:"Hind",sans-serif;font-size:4.6px;color:var(--white)}

.gate-shade{left:0;top:0;width:340px;height:1147px;background:rgba(0,0,0,.74)}
.gate{left:61px;top:75px;width:218px;height:110px;background:var(--white)}
.gate-close{left:269px;top:71px;width:14px;height:14px;border-radius:50%;background:var(--black);border:.8px solid var(--white);color:var(--white);font-family:"Hind",sans-serif;font-size:5px;display:flex;align-items:center;justify-content:center}
.gate-brand{left:61px;top:95px;width:218px;text-align:center;font-size:10px;color:var(--black)}
.gate-title{left:61px;top:116px;width:218px;text-align:center;font-size:8px;font-weight:500;color:var(--black)}
.gate-copy{left:95px;top:131px;width:150px;text-align:center;font-size:3.5px;line-height:7px;color:#333}
.gate-enter{left:135px;top:153px;width:35px;height:13px}
.gate-exit{left:171px;top:153px;width:35px;height:13px}
</style>
</head>
<body>

<section class="panel panel--gate" aria-label="Home page with age confirmation">
  <svg class="backdrop" viewBox="0 0 340 1147" width="340" height="1147" aria-hidden="true">
    <defs>
      <linearGradient id="g-growth-a" x1="0" y1="0" x2="1" y2="1"><stop offset="0" stop-color="#13b812"/><stop offset=".5" stop-color="#2ef01f"/><stop offset="1" stop-color="#119b10"/></linearGradient>
      <linearGradient id="g-news-a" x1="0" y1="0" x2="0" y2="1"><stop offset="0" stop-color="#14c812"/><stop offset="1" stop-color="#26ee1a"/></linearGradient>
      <radialGradient id="g-hero-a" cx=".78" cy=".45" r=".75"><stop offset="0" stop-color="#3f6e30"/><stop offset=".35" stop-color="#22391c"/><stop offset=".7" stop-color="#111611"/><stop offset="1" stop-color="#0a0b0a"/></radialGradient>
    </defs>
    <rect x="0" y="1040" width="340" height="107" fill="#000"/>
    <path d="M0 963 Q170 943 340 963 V1061 Q170 1095 0 1061 Z" fill="url(#g-news-a)"/>
    <path d="M0 560 H340 V742 Q170 780 0 742 Z" fill="#161616"/>
    <path d="M0 742 Q170 780 340 742" fill="none" stroke="#1ed61a" stroke-width="1.2"/>
    <path d="M0 416 Q170 378 340 416 V569 Q170 615 0 569 Z" fill="url(#g-growth-a)"/>
    <path d="M0 0 H340 V224 Q170 266 0 224 Z" fill="url(#g-hero-a)" role="img" aria-label="Photo of hemp leaves in low light"/>
    <path d="M0 224 Q170 266 340 224" fill="none" stroke="#1ed61a" stroke-width="1.6"/>
    <rect x="0" y="0" width="340" height="39" fill="#000"/>
    <line x1="0" y1="39" x2="340" y2="39" stroke="#1ed61a" stroke-width=".8"/>
  </svg>

  <div class="brand header-brand">kestrelbrookhollow.com</div>
  <nav class="nav header-nav"><span class="is-active">Home</span><span>About Us</span><span>Services</span><span>Product</span><span>News</span><span>Contact Us</span></nav>
  <svg class="cart" viewBox="0 0 16 14" aria-hidden="true"><path d="M1 1h3l2 8h8l2-6H5" fill="none" stroke="#1ed61a" stroke-width="1.4"/><circle cx="7" cy="12" r="1.2" fill="#1ed61a"/><circle cx="13" cy="12" r="1.2" fill="#1ed61a"/></svg>

  <div class="about-leaf" role="img" aria-label="Hemp leaf illustration"></div>
  <div class="heading about-title">About</div>
  <div class="heading about-sub">Kestrel Brook Hollow</div>
  <p class="copy about-copy">Sed ut perspiciatis unde omnis iste natus error sit voluptatem accusantium doloremque laudantium, totam rem aperiam, eaque ipsa quae ab illo inventore veritatis et quasi architecto beatae vitae dicta sunt explicabo. Nemo enim ipsam voluptatem quia voluptas sit aspernatur aut odit aut fugit, sed eos qui ratione voluptatem sequi nesciunt. Neque porro quisquam est, qui dolorem ipsum quia dolor sit amet, consectetur, adipisci velit, sed quia non ut labore et dolore magnam aliquam quaerat voluptatem.</p>
  <div class="btn btn--green about-btn">READ MORE</div>

  <div class="growth-visual" role="img" aria-label="Close-up photo of young hemp leaves"></div>
  <div class="heading growth-kicker">Incorporated</div>
  <div class="heading growth-title">Seed to Growth</div>
  <p class="copy growth-copy">Sed ut perspiciatis unde omnis iste natus error sit voluptatem accusantium doloremque laudantium, totam rem aperiam, eaque ipsa quae ab illo inventore veritatis et quasi architecto beatae vitae dicta sunt explicabo. Nemo enim ipsam voluptatem quia voluptas sit aspernatur aut odit aut fugit, sed quia consequuntur magni dolores eos qui ratione voluptatem sequi nesciunt.</p>
  <div class="btn btn--dark growth-btn">READ MORE</div>

  <div class="heading services-title">Our Services</div>
  <div class="services-rule"></div>
  <div class="service service--1">
    <svg class="service-icon" viewBox="0 0 46 46" aria-hidden="true"><circle cx="23" cy="23" r="21" fill="#0d6e0d" stroke="#1ed61a" stroke-width="3"/><rect x="14" y="15" width="10" height="9" fill="none" stroke="#fff" stroke-width="1.2"/><rect x="14" y="23" width="19" height="6" fill="none" stroke="#fff" stroke-width="1.2"/><circle cx="17" cy="30" r="4" fill="#0d6e0d" stroke="#fff" stroke-width="1.2"/><circle cx="30" cy="31" r="2.5" fill="#0d6e0d" stroke="#fff" stroke-width="1.2"/></svg>
    <h3>Services 01</h3><p>Nemo enim ipsam voluptatem quia voluptas sit aspernatur aut odit aut fugit voluptatem sequi nesciunt.</p>
  </div>
  <div class="service service--2">
    <svg class="service-icon" viewBox="0 0 46 46" aria-hidden="true"><circle cx="23" cy="23" r="21" fill="#0d6e0d" stroke="#1ed61a" stroke-width="3"/><path d="M23 32V20M23 22q-7 0-8-7 7 0 8 7zM23 22q7 0 8-7-7 0-8 7M15 32h16" fill="none" stroke="#fff" stroke-width="1.3"/></svg>
    <h3>Services 02</h3><p>Nemo enim ipsam voluptatem quia voluptas sit aspernatur aut odit aut fugit voluptatem sequi nesciunt.</p>
  </div>
  <div class="service service--3">
    <svg class="service-icon" viewBox="0 0 46 46" aria-hidden="true"><circle cx="23" cy="23" r="21" fill="#0d6e0d" stroke="#1ed61a" stroke-width="3"/><path d="M23 30l-3-16 3 4 3-4zM23 30l-9-8 5 1zM23 30l9-8-5 1zM23 30v4" fill="none" stroke="#fff" stroke-width="1.2" stroke-linejoin="round"/></svg>
    <h3>Services 03</h3><p>Nemo enim ipsam voluptatem quia voluptas sit aspernatur aut odit aut fugit voluptatem sequi nesciunt.</p>
  </div>

  <div class="heading news-title"><b>Latest</b> News</div>
  <div class="news-rule"></div>
  <article class="news-card news-card--1"><div class="news-photo news-photo--seed-hands" role="img" aria-label="Gloved hands holding hemp seeds over a sack"></div><h4>SED UT PERSPICIATIS UNDE OMNIS ISTE NATUS ERROR SIT</h4><p>Nemo enim ipsam voluptatem quia voluptas sit aspernatur aut odit aut fugit, sed quia conseq untur voluptatem sequi nesciunt</p><div class="btn btn--green">READ MORE</div></article>
  <article class="news-card news-card--2"><div class="news-photo news-photo--leaves" role="img" aria-label="Field of green hemp leaves"></div><h4>SED UT PERSPICIATIS UNDE OMNIS ISTE NATUS ERROR SIT</h4><p>Nemo enim ipsam voluptatem quia voluptas sit aspernatur aut odit aut fugit, sed quia conseq untur voluptatem sequi nesciunt</p><div class="btn btn--green">READ MORE</div></article>
  <article class="news-card news-card--3"><div class="news-photo news-photo--seeds" role="img" aria-label="Wooden scoop of hemp seeds on burlap"></div><h4>SED UT PERSPICIATIS UNDE OMNIS ISTE NATUS ERROR SIT</h4><p>Nemo enim ipsam voluptatem quia voluptas sit aspernatur aut odit aut fugit, sed quia conseq untur voluptatem sequi nesciunt</p><div class="btn btn--green">READ MORE</div></article>

  <div class="heading news-letter-title">Newsletter Signup</div>
  <div class="news-letter-rule"></div>
  <p class="news-letter-copy">Sed ut perspiciatis unde omnis iste natus error sit voluptatem accusantium doloremque laudantium, totam rem aperiam</p>
  <div class="email-field">Email :</div>
  <div class="btn btn--dark submit-btn">SUBMIT</div>

  <div class="brand footer-brand">kestrelbrookhollow.com</div>
  <nav class="nav footer-nav"><span>Home</span><span>About Us</span><span>Services</span><span>Product</span><span>News</span><span>Contact Us</span></nav>
  <div class="copyright">Copyright © 2020 All right reserved</div>

  <div class="gate-shade"></div>
  <div class="gate" role="dialog" aria-label="Age confirmation"></div>
  <div class="gate-close">x</div>
  <div class="brand gate-brand">kestrelbrookhollow.com</div>
  <div class="heading gate-title">You Must be 21 or older to enter!</div>
  <p class="gate-copy">Sed ut perspiciatis unde omnis iste natus error sit voluptatem accusantium doloremque audantium, totam rem aperiam eaque ipsa quae</p>
  <div class="btn btn--green gate-enter">ENTER</div>
  <div class="btn btn--dark gate-exit">EXIT</div>
</section>

<section class="panel panel--open" aria-label="Home page">
  <svg class="backdrop" viewBox="0 0 340 1147" width="340" height="1147" aria-hidden="true">
    <defs>
      <linearGradient id="g-growth-b" x1="0" y1="0" x2="1" y2="1"><stop offset="0" stop-color="#13b812"/><stop offset=".5" stop-color="#2ef01f"/><stop offset="1" stop-color="#119b10"/></linearGradient>
      <linearGradient id="g-news-b" x1="0" y1="0" x2="0" y2="1"><stop offset="0" stop-color="#14c812"/><stop offset="1" stop-color="#26ee1a"/></linearGradient>
      <radialGradient id="g-hero-b" cx=".78" cy=".45" r=".75"><stop offset="0" stop-color="#3f6e30"/><stop offset=".35" stop-color="#22391c"/><stop offset=".7" stop-color="#111611"/><stop offset="1" stop-color="#0a0b0a"/></radialGradient>
    </defs>
    <rect x="0" y="1040" width="340" height="107" fill="#000"/>
    <path d="M0 963 Q170 943 340 963 V1061 Q170 1095 0 1061 Z" fill="url(#g-news-b)"/>
    <path d="M0 560 H340 V742 Q170 780 0 742 Z" fill="#161616"/>
    <path d="M0 742 Q170 780 340 742" fill="none" stroke="#1ed61a" stroke-width="1.2"/>
    <path d="M0 416 Q170 378 340 416 V569 Q170 615 0 569 Z" fill="url(#g-growth-b)"/>
    <path d="M0 0 H340 V224 Q170 266 0 224 Z" fill="url(#g-hero-b)" role="img" aria-label="Photo of hemp leaves in low light"/>
    <path d="M0 224 Q170 266 340 224" fill="none" stroke="#1ed61a" stroke-width="1.6"/>
    <rect x="0" y="0" width="340" height="39" fill="#000"/>
    <line x1="0" y1="39" x2="340" y2="39" stroke="#1ed61a" stroke-width=".8"/>
  </svg>

  <div class="brand header-brand">kestrelbrookhollow.com</div>
  <nav class="nav header-nav"><span class="is-active">Home</span><span>About Us</span><span>Services</span><span>Product</span><span>News</span><span>Contact Us</span></nav>
  <svg class="cart" viewBox="0 0 16 14" aria-hidden="true"><path d="M1 1h3l2 8h8l2-6H5" fill="none" stroke="#1ed61a" stroke-width="1.4"/><circle cx="7" cy="12" r="1.2" fill="#1ed61a"/><circle cx="13" cy="12" r="1.2" fill="#1ed61a"/></svg>

  <svg class="hero-frame" viewBox="0 0 340 240" width="340" height="240" aria-hidden="true">
    <path d="M89 127 H65 V167 H274 V127 H251" fill="none" stroke="#fff" stroke-width="1"/>
  </svg>
  <div class="brand hero-brand">kestrelbrookhollow</div>
  <div class="hero-tag">PAUSE - PLAY - REWIND</div>

  <div class="about-leaf" role="img" aria-label="Hemp leaf illustration"></div>
  <div class="heading about-title">About</div>
  <div class="heading about-sub">Kestrel Brook Hollow</div>
  <p class="copy about-copy">Sed ut perspiciatis unde omnis iste natus error sit voluptatem accusantium doloremque laudantium, totam rem aperiam, eaque ipsa quae ab illo inventore veritatis et quasi architecto beatae vitae dicta sunt explicabo. Nemo enim ipsam voluptatem quia voluptas sit aspernatur aut odit aut fugit, sed eos qui ratione voluptatem sequi nesciunt. Neque porro quisquam est, qui dolorem ipsum quia dolor sit amet, consectetur, adipisci velit, sed quia non ut labore et dolore magnam aliquam quaerat voluptatem.</p>
  <div class="btn btn--green about-btn">READ MORE</div>

  <div class="growth-visual" role="img" aria-label="Close-up photo of young hemp leaves"></div>
  <div class="heading growth-kicker">Incorporated</div>
  <div class="heading growth-title">Seed to Growth</div>
  <p class="copy growth-copy">Sed ut perspiciatis unde omnis iste natus error sit voluptatem accusantium doloremque laudantium, totam rem aperiam, eaque ipsa quae ab illo inventore veritatis et quasi architecto beatae vitae dicta sunt explicabo. Nemo enim ipsam voluptatem quia voluptas sit aspernatur aut odit aut fugit, sed quia consequuntur magni dolores eos qui ratione voluptatem sequi nesciunt.</p>
  <div class="btn btn--dark growth-btn">READ MORE</div>

  <div class="heading services-title">Our Services</div>
  <div class="services-rule"></div>
  <div class="service service--1">
    <svg class="service-icon" viewBox="0 0 46 46" aria-hidden="true"><circle cx="23" cy="23" r="21" fill="#0d6e0d" stroke="#1ed61a" stroke-width="3"/><rect x="14" y="15" width="10" height="9" fill="none" stroke="#fff" stroke-width="1.2"/><rect x="14" y="23" width="19" height="6" fill="none" stroke="#fff" stroke-width="1.2"/><circle cx="17" cy="30" r="4" fill="#0d6e0d" stroke="#fff" stroke-width="1.2"/><circle cx="30" cy="31" r="2.5" fill="#0d6e0d" stroke="#fff" stroke-width="1.2"/></svg>
    <h3>Services 01</h3><p>Nemo enim ipsam voluptatem quia voluptas sit aspernatur aut odit aut fugit voluptatem sequi nesciunt.</p>
  </div>
  <div class="service service--2">
    <svg class="service-icon" viewBox="0 0 46 46" aria-hidden="true"><circle cx="23" cy="23" r="21" fill="#0d6e0d" stroke="#1ed61a" stroke-width="3"/><path d="M23 32V20M23 22q-7 0-8-7 7 0 8 7zM23 22q7 0 8-7-7 0-8 7M15 32h16" fill="none" stroke="#fff" stroke-width="1.3"/></svg>
    <h3>Services 02</h3><p>Nemo enim ipsam voluptatem quia voluptas sit aspernatur aut odit aut fugit voluptatem sequi nesciunt.</p>
  </div>
  <div class="service service--3">
    <svg class="service-icon" viewBox="0 0 46 46" aria-hidden="true"><circle cx="23" cy="23" r="21" fill="#0d6e0d" stroke="#1ed61a" stroke-width="3"/><path d="M23 30l-3-16 3 4 3-4zM23 30l-9-8 5 1zM23 30l9-8-5 1zM23 30v4" fill="none" stroke="#fff" stroke-width="1.2" stroke-linejoin="round"/></svg>
    <h3>Services 03</h3><p>Nemo enim ipsam voluptatem quia voluptas sit aspernatur aut odit aut fugit voluptatem sequi nesciunt.</p>
  </div>

  <div class="heading news-title"><b>Latest</b> News</div>
  <div class="news-rule"></div>
  <article class="news-card news-card--1"><div class="news-photo news-photo--seed-hands" role="img" aria-label="Gloved hands holding hemp seeds over a sack"></div><h4>SED UT PERSPICIATIS UNDE OMNIS ISTE NATUS ERROR SIT</h4><p>Nemo enim ipsam voluptatem quia voluptas sit aspernatur aut odit aut fugit, sed quia conseq untur voluptatem sequi nesciunt</p><div class="btn btn--green">READ MORE</div></article>
  <article class="news-card news-card--2"><div class="news-photo news-photo--leaves" role="img" aria-label="Field of green hemp leaves"></div><h4>SED UT PERSPICIATIS UNDE OMNIS ISTE NATUS ERROR SIT</h4><p>Nemo enim ipsam voluptatem quia voluptas sit aspernatur aut odit aut fugit, sed quia conseq untur voluptatem sequi nesciunt</p><div class="btn btn--green">READ MORE</div></article>
  <article class="news-card news-card--3"><div class="news-photo news-photo--seeds" role="img" aria-label="Wooden scoop of hemp seeds on burlap"></div><h4>SED UT PERSPICIATIS UNDE OMNIS ISTE NATUS ERROR SIT</h4><p>Nemo enim ipsam voluptatem quia voluptas sit aspernatur aut odit aut fugit, sed quia conseq untur voluptatem sequi nesciunt</p><div class="btn btn--green">READ MORE</div></article>

  <div class="heading news-letter-title">Newsletter Signup</div>
  <div class="news-letter-rule"></div>
  <p class="news-letter-copy">Sed ut perspiciatis unde omnis iste natus error sit voluptatem accusantium doloremque laudantium, totam rem aperiam</p>
  <div class="email-field">Email :</div>
  <div class="btn btn--dark submit-btn">SUBMIT</div>

  <div class="brand footer-brand">kestrelbrookhollow.com</div>
  <nav class="nav footer-nav"><span>Home</span><span>About Us</span><span>Services</span><span>Product</span><span>News</span><span>Contact Us</span></nav>
  <div class="copyright">Copyright © 2020 All right reserved</div>
</section>

</body>
</html>
```